Stationery Design Project for Nimbora, Chicago

Nimbora, a street parking application which helps car drivers find a street parking spot by offering an ideal path along which to look for parking. This path is calculated by our algorithm based on data (e.g. historical data, baseball games schedule, etc.). Along this path the driver will find a spot and will also save 70% of the search time. Customer we target is reg. between 21 and 45 yo.

We envision something young, fresh, bright and original. Slightly abstract maybe. It should represent the idea and elements of finding street parking in the city, e.g. car(s), parking spot, people, city, etc. (just ideas!).

Logo is attached.

Requirement:
- Business Cards (2 Sided Full Color CMYK)
- Letterhead (1 Sided Full Color CMYK)
- Envelope (1 Sided Full Color CMYK)
- Sticker (1 Sided Full Color CMYK), round with a 2inch diameter.

Reason: We're starting to get more and more designs and need more time to look into all of them. Very exciting!! Thanks to everybody!

Hi all, we're in the process of selecting our favs. Though choices!!! Really good submissions. Will keep you posted and sorry for the delay.

Target Market(s)

Car drivers and owners between 21 and 45

Industry/Entity Type

Parking

Requirements
Must have
• Sticker should be round and include company URL nimbora.com and the new logo which we will attach soon.
Should not have
• Should not be too serious or boring.

```html
<!DOCTYPE html>
<html lang="en">
<head>
<meta charset="utf-8">
<title>Nimbora — Business Cards</title>
<link rel="stylesheet" href="https://fonts.googleapis.com/css2?family=Source+Sans+3:wght@400;600;700&display=swap">
<style>
  :root {
    --brand-blue: #1b3597;
    --brand-blue-deep: #0f2270;
    --paper: #ffffff;
    --ink: #1c1c1c;
    --ink-soft: #2a2a2a;
    --backdrop: #e4e4e4;
    --mark-blue: #1f63c9;
  }
  * { box-sizing: border-box; margin: 0; padding: 0; }
  html, body {
    width: 954px; height: 1200px; overflow: hidden;
    background: var(--backdrop);
    font-family: "Source Sans 3", "Myriad Pro", Arial, sans-serif;
  }
  .canvas { position: relative; width: 954px; height: 1200px; }

  .card {
    position: absolute; left: 78px; width: 797px;
    background: var(--brand-blue);
    box-shadow: 0 3px 10px rgba(0,0,0,0.35);
    overflow: hidden;
  }
  .card--front { top: 95px; height: 454px; }
  .card--back  { top: 633px; height: 455px; }

  .brand-panel {
    position: absolute; left: 0; top: 0;
    background: var(--paper);
    border-bottom-right-radius: 22px;
    box-shadow: 4px 5px 10px var(--brand-blue-deep);
  }
  .card--front .brand-panel { width: 647px; height: 205px; }
  .card--back  .brand-panel { width: 744px; height: 237px; }

  .brand-dot {
    position: absolute; border-radius: 50%;
    background: var(--mark-blue);
  }
  .card--front .brand-dot { left: 42px; top: 38px; width: 150px; height: 150px; }
  .card--back  .brand-dot { left: 42px; top: 18px; width: 190px; height: 190px; }

  .brand-name {
    position: absolute; color: var(--ink);
    font-weight: 600; letter-spacing: 1px; line-height: 1;
  }
  .card--front .brand-name { left: 220px; top: 48px; font-size: 104px; }
  .card--back  .brand-name { left: 255px; top: 50px; font-size: 128px; }

  .address {
    position: absolute; left: 39px; top: 374px;
    color: var(--paper); font-size: 22px; line-height: 30px;
  }

  .contact-panel {
    position: absolute; right: 0; bottom: 0;
    background: var(--paper);
    border-top-left-radius: 14px;
    box-shadow: -4px -4px 10px var(--brand-blue-deep);
    color: var(--ink-soft);
  }
  .card--front .contact-panel {
    width: 445px; height: 179px;
    padding: 14px 0 0 22px; font-size: 22px; line-height: 30px;
  }
  .card--back .contact-panel {
    width: 302px; height: 88px;
    padding: 17px 25px 0 0; font-size: 22px; line-height: 30px;
    text-align: right;
  }
  .contact-name { font-size: 25px; font-weight: 700; color: var(--ink); margin-bottom: 10px; }
  .contact-name small { font-size: 19px; font-weight: 700; }
  .contact-phones { margin-bottom: 9px; }
  .label { font-weight: 700; }
  .divider { padding: 0 6px; }
</style>
</head>
<body>
<main class="canvas">

  <section class="card card--front" aria-label="Business card front">
    <div class="brand-panel">
      <span class="brand-dot" aria-hidden="true"></span>
      <span class="brand-name">Nimbora</span>
    </div>
    <p class="address">City Name, Street Name<br>State Name, Country Code</p>
    <div class="contact-panel">
      <p class="contact-name">Your Name - <small>Designation</small></p>
      <p class="contact-phones"><span class="label">t</span> : 123-456-7890<span class="divider">|</span><span class="label">c</span> : 123-456-7890</p>
      <p><span class="label">e</span> : name@website.com</p>
      <p><span class="label">w</span> : www.website.com</p>
    </div>
  </section>

  <section class="card card--back" aria-label="Business card back">
    <div class="brand-panel">
      <span class="brand-dot" aria-hidden="true"></span>
      <span class="brand-name">Nimbora</span>
    </div>
    <div class="contact-panel">
      <p><span class="label">e</span> : name@website.com</p>
      <p><span class="label">w</span> : www.website.com</p>
    </div>
  </section>

</main>
</body>
</html>
```